Industrial Inspection & Testing Company Needs Brochure

We need a brochure design for a company based in Western Pennsylvania, USA. Our company performs services mainly in industrial sites. These can include manufacturing, health & medical, power generation, and more. We use infrared thermography, vibration analysis, ultrasonic thickness testing, dynamic balancing and other practices to provide predictive maintenance to our customers. Please see our website for a more thorough explanation of our services. www.korvaltest.com

Complete list of services:

Infrared Thermal Imaging
Vibration Analysis
High Temperature Video & Photography
High Speed Video
Laser Alignment
Dynamic Balancing
Motor Meggering
Leak Detection
Ultrasonic Thickness Testing
Oil Analysis

KDR, LLC - P.O. Box 4837 - Ashwick Township, PA 16952
Phone: 814-559-3081 / Fax: 814-559-3087

MISSION

KDR, LLC will provide the highest quality, cost effective, world class PdM services in the industry. Our commitment to continuing education and growth will afford our engineers the tools needed to stay on the cutting edge of technology. We believe in the implementation of Predictive Maintenance services to increase overall equipment reliability, reduce costs and improve profitability. Our goal is to provide continuous improvements to these processes. The company will network with various industry professionals to offer the widest range of equipment, training and reliability services available. Meeting these goals will ensure the company’s longevity and allow our valued customers to achieve the cost reduction goals that are needed in today’s competitive marketplace.
HISTORY
KDR, LLC was founded in March 1984, which emerged from the Harlow Forge Industries Incorporated’s Proving Works, Monroeville, Pennsylvania. Its founders headed the Thermography and Photoinstrumentation Department of that facility.
While at the H. F. Industries Proving Works, they established the utilization of thermography as a valuable tool for evaluating equipment and facilities in the steel industry. Their work set the standards for the use of thermography in the steel industry that continues today with KDR. Although the original thermographic equipment was crude, bulky and slow, KDR has maintained its position as an industry leader. Today KDR uses the most technologically advanced infrared systems available for on-site nondestructive industrial inspections.
In addition, while at H. F. Industries Proving, the founders of KDR pioneered the use of photographic cameras and high-speed motion pictures as another form of a predictive and preventative maintenance tool. Specially constructed camera systems with thermal protective housings were developed for inspecting blast furnace interior stockline armor areas, stove domes, and other high-temperature areas.
Today KDR remains on the cutting-edge in providing a wide range of nondestructive inspection services to industry.

***All of the photos and documents attached were either shot by us or purchased stock photos***

I realize that only a few images might be used, I just wanted to upload many to give designers a broad range to choose from.

Target Market(s)

Large industrial customers who use large amounts of electricity, heavy duty machinery, or both.

Industry/Entity Type

Industrial

Requirements
Must have
• Need a 3 full page tri-fold design (not skinny column tri-fold)

Contact information for our company, list of our services, our logo (possible redesign of logo), photos from our inspections that will be attached.
Nice to have
• List of services, breif explanation of each with graphical representation, contact information

```html
<!DOCTYPE html>
<html lang="en">
<head>
<meta charset="utf-8">
<title>KDR, LLC – Tri-fold Brochure</title>
<link rel="stylesheet" href="https://fonts.googleapis.com/css2?family=Open+Sans:wght@400;600;700&family=Archivo+Narrow:wght@400;600;700&display=swap">
<style>
  :root {
    --page-bg: #e6e6e6;
    --sheet: #ffffff;
    --bar-slate: #3f4452;
    --bar-blue: #5a8bc9;
    --bar-violet: #7b73c4;
    --bar-cyan: #2ca8e0;
    --bar-mist: #d9dee8;
    --tile-sky: #b9d4ec;
    --tile-lavender: #b9b5e0;
    --tile-azure: #8ccbef;
    --tile-pale: #eef0f4;
    --navy: #24287e;
    --ink: #333333;
    --muted: #666666;
    --red: #d72a2a;
    --sw-purple: #6d2c91;
    --sw-blue: #2a62b0;
    --sw-orange: #f08a1c;
    --sw-red: #e0262b;
    --sw-yellow: #ffe419;
  }
  * { margin: 0; padding: 0; box-sizing: border-box; }
  html, body { width: 835px; height: 1200px; overflow: hidden; }
  body {
    background: var(--page-bg);
    font-family: "Open Sans", Arial, sans-serif;
    color: var(--ink);
    position: relative;
  }
  .sheet {
    position: absolute;
    left: 65px;
    width: 703px;
    height: 501px;
    background: var(--sheet);
    box-shadow: 0 2px 6px rgba(0,0,0,.18);
  }
  .sheet--outside { top: 63px; }
  .sheet--inside { top: 608px; }
  .abs { position: absolute; }

  .tile { position: absolute; }
  .bar-slate { background: var(--bar-slate); }
  .bar-blue { background: var(--bar-blue); }
  .bar-violet { background: var(--bar-violet); }
  .bar-cyan { background: var(--bar-cyan); }
  .bar-mist { background: var(--bar-mist); }

  .photo { position: absolute; }

  /* services lists (outside) */
  .services-title {
    position: absolute; left: 13px; top: 62px;
    font-size: 15px; font-weight: 700; color: var(--navy); line-height: 1;
  }
  .service-list { list-style: none; }
  .front-list .service-list li {
    font-family: "Archivo Narrow", "Arial Narrow", sans-serif;
    font-size: 7.8px; line-height: 11.1px; color: var(--ink);
    padding-left: 7px; position: relative; white-space: nowrap;
  }
  .front-list .service-list li::before {
    content: ""; position: absolute; left: 0; top: 4px; width: 3.2px; height: 3.2px; background: var(--navy);
  }
  .front-list .service-list--main li { line-height: 12.6px; }
  .front-list .service-list--main li::before { top: 4.7px; }
  .front-list .group-title {
    font-family: "Archivo Narrow", "Arial Narrow", sans-serif;
    font-size: 7.8px; line-height: 11px; color: var(--red); font-weight: 600; white-space: nowrap;
  }

  /* contact */
  .contact {
    position: absolute; right: 233px; top: 150px; text-align: right;
    color: var(--navy); font-size: 9.4px; line-height: 11.6px; font-weight: 700; font-style: normal;
  }
  .contact .web { margin-top: 11px; }

  /* hero */
  .hero {
    position: absolute; left: 477px; top: 11px; width: 226px; height: 249px;
    background: linear-gradient(180deg, #3e3bb0 0%, #2a2a8a 45%, #1a2060 75%, #2c3b6a 100%);
  }
  .hero__tag {
    position: absolute; right: 8px; top: 12px; text-align: right; color: #fff;
    font-family: "Archivo Narrow", "Arial Narrow", sans-serif; line-height: 1;
  }
  .hero__tag .big { display: block; font-size: 21px; letter-spacing: .2px; }
  .hero__tag .small { display: block; font-size: 13.5px; font-weight: 700; margin-top: 2px; }

  .swatches { position: absolute; display: flex; }
  .swatches span { display: block; }

  .brand {
    position: absolute; left: 570px; top: 400px; display: flex; align-items: center; gap: 8px;
  }
  .brand__dot { width: 46px; height: 46px; border-radius: 50%; background: var(--sw-blue); }
  .brand__name { font-size: 46px; font-weight: 700; color: var(--sw-blue); line-height: 1; }

  /* inside */
  .heading { font-weight: 400; color: var(--navy); line-height: 1; }
  .mission-title { position: absolute; left: 18px; top: 16px; font-size: 15px; }
  .body-copy { font-size: 6px; line-height: 7.8px; color: var(--muted); text-align: justify; }
  .mission-copy { position: absolute; left: 18px; top: 34px; width: 150px; }

  .inside-services-title { position: absolute; left: 180px; top: 46px; font-size: 15px; }
  .inside-list { position: absolute; }
  .inside-list .service-list li {
    font-size: 6.4px; line-height: 8.6px; padding-left: 6px; position: relative; white-space: nowrap;
  }
  .inside-list .service-list li::before {
    content: ""; position: absolute; left: 0; top: 3px; width: 2.6px; height: 2.6px; background: var(--navy);
  }
  .inside-list .group-title { font-size: 6.4px; line-height: 9px; font-weight: 700; color: var(--red); white-space: nowrap; }

  .history-title { position: absolute; left: 418px; top: 222px; font-size: 22px; color: var(--red); }
  .history-copy { position: absolute; left: 418px; top: 250px; width: 276px; }
</style>
</head>
<body>

<section class="sheet sheet--outside" aria-label="Brochure outside">
  <div class="tile" style="left:7px;top:11px;width:92px;height:14px;background:var(--bar-mist);"></div>
  <div class="tile" style="left:110px;top:11px;width:100px;height:54px;background:var(--tile-sky);"></div>
  <div class="tile" style="left:221px;top:11px;width:63px;height:105px;background:var(--tile-lavender);"></div>
  <div class="tile" style="left:295px;top:11px;width:82px;height:132px;background:var(--tile-azure);"></div>
  <div class="tile" style="left:388px;top:11px;width:82px;height:132px;background:var(--tile-pale);"></div>

  <h2 class="services-title">services</h2>
  <div class="front-list abs" style="left:12px;top:80px;">
    <ul class="service-list service-list--main">
      <li>Infrared Thermal Imaging</li>
      <li>Vibration Analysis</li>
      <li>High Temperature Video &amp; Photography</li>
      <li>High Speed Video</li>
      <li>Laser Alignment</li>
      <li>Dynamic Balancing</li>
      <li>Motor Meggering</li>
      <li>Leak Detection</li>
      <li>Ultrasonic Thickness Testing</li>
      <li>Oil Analysis</li>
    </ul>
  </div>

  <div class="front-list abs" style="left:146px;top:131px;">
    <p class="group-title" style="padding-left:2px;">Condition Monitoring &amp; PdM</p>
    <ul class="service-list">
      <li>Ultrasonic Thickness Testing</li>
      <li>Oil Analysis</li>
      <li>Infrared Thermal Imaging</li>
      <li>High Temperature Video &amp; Photography</li>
      <li>Vibration Analysis</li>
    </ul>
    <p class="group-title" style="margin-top:6px;padding-left:2px;">Precision Maintenance</p>
    <ul class="service-list">
      <li>Laser Alignment</li>
      <li>Balancing</li>
      <li>Leak Detection</li>
      <li>Lubrication</li>
      <li>Training</li>
    </ul>
  </div>

  <address class="contact">
    KDR, LLC<br>
    P.O. Box 4837<br>
    Ashwick Township, PA 16952<br>
    Phone: 814-559-3081<br>
    Fax: 814-559-3087
    <div class="web">www.korvaltest.com</div>
  </address>

  <div class="hero" role="img" aria-label="Power station chimneys lit at dusk over water">
    <div class="hero__tag">
      <span class="big">HIGHEST QUALITY</span>
      <span class="big">COST EFFECTIVE</span>
      <span class="small">WORLD CLASS PDM SERVICES</span>
    </div>
  </div>

  <div class="tile bar-slate" style="left:21px;top:271px;width:82px;height:16px;"></div>
  <div class="tile bar-blue" style="left:110px;top:271px;width:82px;height:16px;"></div>
  <div class="tile bar-violet" style="left:202px;top:271px;width:82px;height:16px;"></div>
  <div class="tile bar-cyan" style="left:295px;top:271px;width:82px;height:16px;"></div>
  <div class="tile bar-mist" style="left:388px;top:271px;width:82px;height:16px;"></div>

  <div class="photo" role="img" aria-label="Steel mill blast furnace structure" style="left:21px;top:295px;width:82px;height:192px;background:linear-gradient(180deg,#7d8c9c,#4a4a4e 60%,#2e2c2a);"></div>
  <div class="photo" role="img" aria-label="Tall industrial smokestack against blue sky" style="left:110px;top:295px;width:82px;height:192px;background:linear-gradient(180deg,#4f86c8,#8fb4dc 55%,#6b6258);"></div>
  <div class="photo" role="img" aria-label="Power line pylon silhouetted at sunset" style="left:202px;top:295px;width:82px;height:192px;background:linear-gradient(180deg,#2f3f8a,#c0609a 45%,#f29a3a 75%,#3a2b2a);"></div>
  <div class="photo" role="img" aria-label="Water treatment tanks on green lawn" style="left:295px;top:295px;width:82px;height:192px;background:linear-gradient(180deg,#8db8e0,#d6d9d6 50%,#7aa04e);"></div>
  <div class="photo" role="img" aria-label="Cooling towers in a hazy valley" style="left:388px;top:295px;width:82px;height:192px;background:linear-gradient(180deg,#9ec0e0,#c9cfd2 55%,#9a8a6a);"></div>

  <div class="swatches" style="left:480px;top:294px;">
    <span style="width:21px;height:47px;background:var(--sw-purple);"></span>
    <span style="width:21px;height:47px;background:var(--sw-blue);"></span>
    <span style="width:21px;height:47px;background:var(--sw-orange);"></span>
    <span style="width:21px;height:47px;background:var(--sw-red);"></span>
    <span style="width:21px;height:47px;background:var(--sw-yellow);"></span>
  </div>

  <div class="brand" aria-label="KDR">
    <span class="brand__dot"></span>
    <span class="brand__name">KDR</span>
  </div>
</section>

<section class="sheet sheet--inside" aria-label="Brochure inside">
  <h2 class="heading mission-title">Our Mission</h2>
  <p class="body-copy mission-copy">KDR, LLC will provide the highest quality, cost effective, world class PdM services in the industry. Our commitment to continuing education and growth will afford our engineers the tools needed to stay on the cutting edge of technology. We believe in the implementation of Predictive Maintenance services to increase overall equipment reliability, reduce costs and improve profitability. Our goal is to provide continuous improvements to these processes. The company will network with various industry professionals to offer the widest range of equipment, training and reliability services available. Meeting these goals will ensure the company’s longevity and allow our valued customers to achieve the cost reduction goals that are needed in today’s competitive marketplace.</p>

  <h2 class="heading inside-services-title">Our Services</h2>
  <div class="inside-list" style="left:180px;top:69px;">
    <p class="group-title">Thermography</p>
    <ul class="service-list">
      <li>Thermographic Tour</li>
      <li>Building Inspections</li>
      <li>Electrical Inspections</li>
      <li>Roof Inspections</li>
      <li>Infrared Thermal Imaging</li>
    </ul>
    <p class="group-title" style="margin-top:6px;">Condition Monitoring &amp; Pdm</p>
    <ul class="service-list">
      <li>Vibration Analysis</li>
      <li>Oil Analysis</li>
      <li>Ultrasonic Leak Detection</li>
      <li>Ultrasonic Thickness Testing</li>
    </ul>
  </div>
  <div class="inside-list" style="left:283px;top:94px;">
    <p class="group-title">Precision Maintenance</p>
    <ul class="service-list">
      <li>Precision Laser Alignment</li>
      <li>Balancing</li>
    </ul>
    <p class="group-title" style="margin-top:6px;">Video Inspection</p>
    <ul class="service-list">
      <li>Specialty Video</li>
      <li>High Temp Video</li>
      <li>Inspections</li>
      <li>Slow Motion Study</li>
    </ul>
  </div>

  <div class="tile bar-slate" style="left:369px;top:36px;width:61px;height:12px;"></div>
  <div class="tile bar-blue" style="left:438px;top:36px;width:61px;height:12px;"></div>
  <div class="tile bar-violet" style="left:507px;top:36px;width:61px;height:12px;"></div>
  <div class="tile bar-cyan" style="left:576px;top:36px;width:61px;height:12px;"></div>
  <div class="tile bar-mist" style="left:645px;top:36px;width:58px;height:12px;"></div>

  <div class="photo" role="img" aria-label="Turbine hall interior with piping" style="left:369px;top:57px;width:61px;height:149px;background:linear-gradient(180deg,#cfd6e0,#8b94a6 50%,#4c4f5c);"></div>
  <div class="photo" role="img" aria-label="Infrared thermal image of electrical equipment" style="left:438px;top:57px;width:61px;height:149px;background:linear-gradient(180deg,#3a1a7a,#9a2aa8 45%,#e25a5a 75%,#2a1660);"></div>
  <div class="photo" role="img" aria-label="Glowing furnace interior" style="left:507px;top:57px;width:61px;height:149px;background:linear-gradient(180deg,#f6c66a,#e08a2a 50%,#7a3a12);"></div>
  <div class="photo" role="img" aria-label="Electrical switchgear cabinet" style="left:576px;top:57px;width:61px;height:149px;background:linear-gradient(180deg,#6a8ca8,#3e5a70 55%,#27394a);"></div>
  <div class="photo" role="img" aria-label="Molten steel pour in a mill" style="left:645px;top:57px;width:58px;height:149px;background:linear-gradient(180deg,#8a4a2a,#d8642a 45%,#4a2a1c);"></div>

  <div class="photo" role="img" aria-label="Cooling towers and power plant lit at night" style="left:0;top:227px;width:404px;height:274px;background:linear-gradient(180deg,#1c2848 0%,#2e4470 40%,#6c7a8e 62%,#3a3430 85%,#1e1a18 100%);"></div>

  <div class="swatches" style="left:15px;top:463px;">
    <span style="width:16px;height:33px;background:var(--sw-purple);"></span>
    <span style="width:16px;height:33px;background:var(--sw-blue);"></span>
    <span style="width:16px;height:33px;background:var(--sw-orange);"></span>
    <span style="width:16px;height:33px;background:var(--sw-red);"></span>
    <span style="width:16px;height:33px;background:var(--sw-yellow);"></span>
  </div>

  <h2 class="heading history-title">History</h2>
  <p class="body-copy history-copy">KDR, LLC will provide the highest quality, cost effective, world class PdM services in the industry. Our commitment to continuing education and growth will afford our engineers the tools needed to stay on the cutting edge of technology. We believe in the implementation of Predictive Maintenance services to increase overall equipment reliability, reduce costs and improve profitability. Our goal is to provide continuous improvements to these processes. The company will network with various industry professionals to offer the widest range of equipment, training and reliability services available. Meeting these goals will ensure the company’s longevity and allow our valued customers to achieve the cost reduction goals that are needed in today’s competitive marketplace. KDR, LLC was founded in March 1984, which emerged from the Harlow Forge Industries Incorporated’s Proving Works, Monroeville, Pennsylvania. Its founders headed the Thermography and Photoinstrumentation Department of that facility. While at the H. F. Industries Proving Works, they established the utilization of thermography as a valuable tool for evaluating equipment and facilities in the steel industry. Their work set the standards for the use of thermography in the steel industry that continues today with KDR. Although the original thermographic equipment was crude, bulky and slow, KDR has maintained its position as an industry leader. Today KDR uses the most technologically advanced infrared systems available for on-site nondestructive industrial inspections. In addition, while at H. F. Industries Proving, the founders of KDR pioneered the use of photographic cameras and high-speed motion pictures as another form of a predictive and preventative maintenance tool. Specially constructed camera systems with thermal protective housings were developed for inspecting blast furnace interior stockline armor areas, stove domes, and other high-temperature areas. Today KDR remains on the cutting edge in providing a wide range of nondestructive inspection services to industry.</p>

  <div class="tile bar-slate" style="left:369px;top:484px;width:61px;height:10px;"></div>
  <div class="tile bar-blue" style="left:438px;top:484px;width:61px;height:10px;"></div>
  <div class="tile bar-violet" style="left:507px;top:484px;width:61px;height:10px;"></div>
  <div class="tile bar-cyan" style="left:576px;top:484px;width:61px;height:10px;"></div>
  <div class="tile bar-mist" style="left:645px;top:484px;width:58px;height:10px;"></div>
</section>

</body>
</html>
```